Vehicle Rental Hire in the Algarve - Portugal

We are opening a Vehicle Rental company in the Algarve - Portugal - this will attract both locals and Tourists visiting. So we want this website to capture the beautiful location we will be set in, along with the familiarity of a vehicle rental company. And to keep a colour scheme in Line with out Logo. We are Quenmira Vehicle Rental.

Industry/Entity Type

Vehicle Rental

Number of Pages Required

1 page

Requirements
Must have
• must be professional, and simple to use navigation bar - must also have a "make a reservation" box - similar to the screenshot attached - Under our logo it must read "Vehicle Rental"
Nice to have
• It needs to be in a colour scheme that fits in with our logo

```html
<!DOCTYPE html>
<html lang="en">
<head>
<meta charset="utf-8">
<title>Quenmira Vehicle Rental</title>
<link href="https://fonts.googleapis.com/css2?family=Marcellus&family=Poppins:wght@400;500;600&display=swap" rel="stylesheet">
<style>
:root{
  --blue:#1a10e0;
  --blue-deep:#2a1fc8;
  --red:#c1312b;
  --ink:#1c1c1c;
  --text:#333;
  --grey:#f3f3f3;
  --footer:#1d1d1d;
  --white:#fff;
}
*{box-sizing:border-box;margin:0;padding:0}
html,body{width:1200px;height:2770px;overflow:hidden;background:var(--white)}
body{position:relative;font-family:'Poppins',sans-serif;color:var(--text)}
.abs{position:absolute}
.serif{font-family:'Marcellus',serif}
.btn{position:absolute;display:flex;align-items:center;justify-content:center;border-radius:24px;font-family:'Marcellus',serif;font-size:16px;color:var(--white);background:var(--blue)}

/* header */
.site-header{position:absolute;left:0;top:0;width:1200px;height:108px;background:var(--white)}
.brand{position:absolute;left:124px;top:28px;display:flex;align-items:center;gap:10px}
.brand-dot{width:44px;height:44px;border-radius:50%;border:3px solid var(--blue)}
.brand-name{font-family:'Poppins',sans-serif;font-weight:600;font-size:22px;color:var(--blue);line-height:1}
.brand-sub{font-size:11px;color:var(--red);margin-top:4px}
.nav a{position:absolute;top:44px;font-size:16px;font-weight:500;color:var(--ink);text-decoration:none}
.login{left:980px;top:32px;width:107px;height:46px;font-family:'Poppins',sans-serif;font-weight:500;font-size:15px}

/* hero */
.hero{position:absolute;left:0;top:108px;width:1200px;height:600px;
  background:linear-gradient(135deg,#2b24c9 0%,#3a2ff0 40%,#2218c0 75%,#1d14a8 100%)}
.hero-photo{position:absolute;left:0;top:0;width:1200px;height:600px;
  background:radial-gradient(ellipse at 80% 30%,rgba(90,80,255,.5),transparent 60%),radial-gradient(ellipse at 20% 80%,rgba(20,10,120,.5),transparent 60%)}
.fleet{position:absolute;left:516px;top:322px;width:684px;height:258px;border-radius:8px;
  background:linear-gradient(180deg,#e8e8ee,#b9bac4)}
.hero-title{position:absolute;left:600px;top:168px;font-size:43px;line-height:52px;color:var(--white)}
.hero-text{position:absolute;left:602px;top:282px;width:470px;font-size:13.5px;line-height:26px;color:var(--white)}
.get-started{left:602px;top:350px;width:140px;height:47px;background:transparent;border:2px solid var(--white)}

/* reservation */
.reserve{position:absolute;left:112px;top:108px;width:385px;height:600px;background:var(--red)}
.reserve h2{position:absolute;left:34px;top:50px;font-family:'Marcellus',serif;font-weight:400;font-size:27px;color:var(--white)}
.field{position:absolute;background:var(--white);border-radius:3px;height:43px;padding:0 12px;
  display:flex;align-items:center;justify-content:space-between;font-size:12px;color:#666}
.field svg{width:8px;height:8px}
.label{position:absolute;font-size:14.5px;color:var(--white)}
.submit{left:23px;top:520px;width:107px;height:46px;font-family:'Poppins',sans-serif;font-weight:500;font-size:15px}

/* about */
.section-title{position:absolute;font-family:'Marcellus',serif;font-size:31px;color:var(--ink)}
.body-copy{position:absolute;font-size:16px;line-height:25.8px;color:var(--text)}
.coast{position:absolute;left:647px;top:813px;width:398px;height:398px;border-radius:50%;
  background:linear-gradient(180deg,#3b86d8 0%,#8cc3ea 30%,#2bb3b0 50%,#c9a86a 70%,#6c8a3a 100%)}

/* vehicles */
.vehicles{position:absolute;left:0;top:1317px;width:1200px;height:540px;background:var(--grey)}
.card{position:absolute;top:158px;width:299px}
.card-back{height:164px;border-radius:14px}
.card-car{position:absolute;left:18px;top:60px;width:263px;height:100px;border-radius:40px 50px 14px 14px;background:linear-gradient(180deg,#f4f4f6,#bfc0c6)}
.stock{position:absolute;top:248px;width:100%;text-align:center;font-weight:600;font-size:17px;color:var(--blue)}
.kind{position:absolute;top:274px;width:100%;text-align:center;font-weight:500;font-size:30px;color:var(--ink)}

/* what we do */
.what{position:absolute;left:0;top:1857px;width:1200px;height:533px;background:linear-gradient(90deg,#fff 45%,#eef0f3 100%)}
.lot{position:absolute;left:157px;top:94px;width:389px;height:328px;
  background:linear-gradient(180deg,#3a3f57 0%,#c8302c 40%,#2f5fb0 55%,#8f8678 80%,#a59c8c 100%)}

/* footer */
.site-footer{position:absolute;left:0;top:2390px;width:1200px;height:380px;background:var(--footer);color:var(--white)}
.foot-brand{position:absolute;left:132px;top:98px;display:flex;align-items:center;gap:10px}
.foot-brand .brand-dot{border-color:var(--white)}
.foot-brand .brand-name{color:var(--white)}
.social{position:absolute;top:202px;width:40px;height:40px;border-radius:50%;background:var(--white)}
.foot-head{position:absolute;top:74px;font-size:18px;font-weight:600}
.foot-links a{position:absolute;left:418px;font-size:13px;color:var(--white);text-decoration:none}
.contact-item{position:absolute;left:629px;display:flex;gap:14px;font-size:14px;line-height:26px}
.contact-item svg{flex:none;margin-top:5px}
.news{position:absolute;left:863px;top:124px;width:225px;height:41px;border-radius:5px;background:var(--white);overflow:hidden}
.news span{position:absolute;left:14px;top:11px;font-size:14px;color:#777}
.news-btn{position:absolute;right:0;top:0;width:54px;height:41px;background:var(--red);display:flex;align-items:center;justify-content:center}
.divider{position:absolute;left:112px;top:292px;width:976px;height:1px;background:#3a3a3a}
.copyright{position:absolute;left:0;top:327px;width:1200px;text-align:center;font-size:14px}
</style>
</head>
<body>

<header class="site-header">
  <div class="brand">
    <div class="brand-dot"></div>
    <div><div class="brand-name">QUENMIRA</div><div class="brand-sub">Vehicle Rental</div></div>
  </div>
  <nav class="nav">
    <a style="left:446px">Home</a>
    <a style="left:538px">About Us</a>
    <a style="left:651px">Services</a>
    <a style="left:761px">Blog</a>
    <a style="left:840px">Contact Us</a>
  </nav>
  <div class="btn login">LOG IN</div>
</header>

<section class="hero">
  <div class="hero-photo" role="img" aria-label="Algarve coastline with cliffs and sea, tinted blue"></div>
  <div class="fleet" role="img" aria-label="White truck, van and small van lined up"></div>
</section>
<h1 class="hero-title serif" style="font-weight:400">QUENMIRA VEHICLE<br>RENTAL</h1>
<p class="hero-text">Lorem ipsum dolor sit amet, consectetur adipiscing elit, sed do eiusmod tempor incididunt ut labore et dolore magna aliqua.</p>
<div class="btn get-started">GET STARTED</div>

<form class="reserve">
  <h2>Make a Reservation</h2>
  <div class="field" style="left:23px;top:107px;width:338px">Pick up location<svg viewBox="0 0 8 8"><path d="M1 2.5l3 3 3-3" stroke="#666" fill="none"/></svg></div>
  <div class="field" style="left:23px;top:184px;width:338px">Drivers's age<svg viewBox="0 0 8 8"><path d="M1 2.5l3 3 3-3" stroke="#666" fill="none"/></svg></div>
  <div class="label" style="left:35px;top:252px">Vehicle category</div>
  <div class="field" style="left:23px;top:279px;width:338px">All<svg viewBox="0 0 8 8"><path d="M1 2.5l3 3 3-3" stroke="#666" fill="none"/></svg></div>
  <div class="label" style="left:35px;top:343px">Pick up date</div>
  <div class="label" style="left:216px;top:343px">Hour</div>
  <div class="field" style="left:23px;top:370px;width:157px">dd-mm-yyyy</div>
  <div class="field" style="left:204px;top:370px;width:157px">9:00<svg viewBox="0 0 8 8"><path d="M1 2.5l3 3 3-3" stroke="#666" fill="none"/></svg></div>
  <div class="label" style="left:35px;top:431px">Drop off date</div>
  <div class="label" style="left:216px;top:431px">Hour</div>
  <div class="field" style="left:23px;top:457px;width:157px">dd-mm-yyyy</div>
  <div class="field" style="left:204px;top:457px;width:157px">9:00<svg viewBox="0 0 8 8"><path d="M1 2.5l3 3 3-3" stroke="#666" fill="none"/></svg></div>
  <div class="btn submit">SUBMIT</div>
</form>

<section class="about">
  <h2 class="section-title" style="left:114px;top:836px;font-weight:400">ABOUT QUENMIRA LIMITADA</h2>
  <p class="body-copy" style="left:114px;top:900px;width:465px">Lorem ipsum dolor sit amet, consectetur adipiscing elit, sed do eiusmod tempor incididunt ut labore et dolore magna aliqua. Ut enim ad minim veniam, quis nostrud exercitation ullamco laboris nisi ut aliquip ex ea commodo consequat. Duis aute irure dolor in reprehenderit in voluptate velit esse cillum dolore eu fugiat nulla pariatur. Excepteur sint occaecat cupidatat non proident, sunt in culpa qui officia deserunt mollit anim id est laborum.</p>
  <div class="btn" style="left:114px;top:1134px;width:139px;height:47px">LEARN MORE</div>
  <div class="coast" role="img" aria-label="Algarve beach with golden rock formations and turquoise water"></div>
  <svg class="abs" style="left:636px;top:802px" width="420" height="420" viewBox="0 0 420 420">
    <path d="M20 124 A208 208 0 0 1 400 124" stroke="var(--blue)" stroke-width="5" fill="none"/>
    <path d="M12 270 A208 208 0 0 0 408 270" stroke="var(--blue)" stroke-width="5" fill="none"/>
  </svg>
</section>

<section class="vehicles">
  <h2 class="section-title" style="left:0;top:76px;width:1200px;text-align:center;font-weight:400">VEHICLE RENTAL</h2>
  <div class="card" style="left:112px">
    <div class="card-back" style="background:var(--ink)"></div>
    <div class="card-car" role="img" aria-label="White SUV"></div>
    <div class="stock">0 in Stock</div><div class="kind">Sedans</div>
  </div>
  <div class="card" style="left:450px">
    <div class="card-back" style="background:var(--red)"></div>
    <div class="card-car" role="img" aria-label="White sedan"></div>
    <div class="stock">0 in Stock</div><div class="kind">SUVs</div>
  </div>
  <div class="card" style="left:788px">
    <div class="card-back" style="background:var(--ink)"></div>
    <div class="card-car" role="img" aria-label="White cargo van"></div>
    <div class="stock">0 in Stock</div><div class="kind">Trucks</div>
  </div>
</section>

<section class="what">
  <svg class="abs" style="left:112px;top:80px" width="460" height="360" viewBox="0 0 460 360">
    <path d="M60 40 A140 140 0 0 0 60 280" stroke="var(--red)" stroke-width="12" fill="none"/>
    <path d="M446 132 V357 H204 V330" stroke="var(--red)" stroke-width="4" fill="none"/>
  </svg>
  <div class="lot" role="img" aria-label="Row of parked red, blue and white vans"></div>
  <h2 class="section-title" style="left:631px;top:89px;font-weight:400">WHAT WE DO</h2>
  <p class="body-copy" style="left:631px;top:152px;width:465px">Lorem ipsum dolor sit amet, consectetur adipiscing elit, sed do eiusmod tempor incididunt ut labore et dolore magna aliqua. Ut enim ad minim veniam, quis nostrud exercitation ullamco laboris nisi ut aliquip ex ea commodo consequat. Duis aute irure dolor in reprehenderit in voluptate velit esse cillum dolore eu fugiat nulla pariatur. Excepteur sint occaecat cupidatat non proident, sunt in culpa qui officia deserunt mollit anim id est laborum.</p>
  <div class="btn" style="left:631px;top:388px;width:139px;height:47px">LEARN MORE</div>
</section>

<footer class="site-footer">
  <div class="foot-brand">
    <div class="brand-dot"></div>
    <div class="brand-name">QUENMIRA</div>
  </div>
  <div class="social" style="left:112px"></div>
  <div class="social" style="left:167px"></div>
  <div class="social" style="left:222px"></div>
  <div class="social" style="left:277px"></div>

  <div class="foot-head" style="left:417px">QUICK LINKS</div>
  <nav class="foot-links">
    <a style="top:124px">Home</a>
    <a style="top:150px">About Us</a>
    <a style="top:176px">Services</a>
    <a style="top:202px">Blog</a>
    <a style="top:228px">Contact Us</a>
  </nav>

  <div class="foot-head" style="left:619px">CONTACT US</div>
  <div class="contact-item" style="top:127px">
    <svg width="16" height="20" viewBox="0 0 16 20"><path d="M8 0a7 7 0 0 0-7 7c0 5 7 13 7 13s7-8 7-13a7 7 0 0 0-7-7zm0 10a3 3 0 1 1 0-6 3 3 0 0 1 0 6z" fill="#fff"/></svg>
    <span>Lorem ipsum dolor sit<br>amet, consectetur</span></div>
  <div class="contact-item" style="top:190px">
    <svg width="18" height="18" viewBox="0 0 24 24"><path d="M6.6 10.8a15 15 0 0 0 6.6 6.6l2.2-2.2a1 1 0 0 1 1-.25 11 11 0 0 0 3.6.6 1 1 0 0 1 1 1V20a1 1 0 0 1-1 1A17 17 0 0 1 3 4a1 1 0 0 1 1-1h3.5a1 1 0 0 1 1 1c0 1.25.2 2.45.6 3.6a1 1 0 0 1-.25 1z" fill="#fff"/></svg>
    <span>1 (555) 014 2290</span></div>
  <div class="contact-item" style="top:224px">
    <svg width="18" height="14" viewBox="0 0 18 14"><rect width="18" height="14" rx="1" fill="#fff"/><path d="M1 1l8 6 8-6" stroke="#1d1d1d" stroke-width="1.5" fill="none"/></svg>
    <span>info@quenmira-rental.pt</span></div>

  <div class="foot-head" style="left:863px">NEWSLETTER</div>
  <div class="news"><span>Enter email</span>
    <div class="news-btn"><svg width="16" height="12" viewBox="0 0 18 14"><rect width="18" height="14" rx="1" fill="#fff"/><path d="M1 1l8 6 8-6" stroke="#c1312b" stroke-width="1.5" fill="none"/></svg></div>
  </div>

  <div class="divider"></div>
  <div class="copyright">©Copyrights 2024 &nbsp;Quenmira Limitada &nbsp;| &nbsp;&nbsp;All Rights Reserved</div>
</footer>

</body>
</html>
```